Heritage Hollow Business Cards

Require a business card design. <br/><br/>Needs to include logo (either round or long version) plus these details:<br/>Maya Torvell<br/>Heritage Hollow<br/>maya@kelvadtrading.com.au<br/>02 6481 7395<br/>PO Box Glenwarra NSW 2791<br/>www.heritagehollow.com.au<br/><br/>I need in an editable format so that I can create for multiple staff members. <br/><br/>

Target Market(s)

We are an online store selling renovation products to home owners are builders. Looking for a classic classy design.

Industry/Entity Type

Home And Garden

Contact Information for Business Card

Maya Torvell
Heritage Hollow
maya@kelvadtrading.com.au
02 6481 7395
PO Box Glenwarra NSW 2791
www.heritagehollow.com.au

Colors

Designer to choose colors to be used in the design.

Requirements
Must have
• Must include Logo.

```html
<!DOCTYPE html>
<html lang="en">
<head>
<meta charset="utf-8">
<title>Heritage Hollow Business Cards</title>
<link rel="stylesheet" href="https://fonts.googleapis.com/css2?family=Montserrat:wght@400;500;600;700&display=swap">
<style>
  :root {
    --stage: #2a2a2a;
    --card-black: #0d0d0d;
    --card-white: #ffffff;
    --ink: #1e1e1e;
    --ink-soft: #4a4a4a;
    --sage: #4f6e60;
    --band-dark: #231f1f;
    --line-light: #d9d9d9;
  }
  * { box-sizing: border-box; margin: 0; padding: 0; }
  html, body { width: 1200px; height: 900px; overflow: hidden; }
  body {
    background: var(--stage);
    font-family: "Montserrat", sans-serif;
    position: relative;
  }
  .card {
    position: absolute;
    left: 285px;
    width: 630px;
    height: 360px;
    overflow: hidden;
    box-shadow: 0 10px 30px rgba(0,0,0,0.45);
  }
  .card-front { top: 70px; background: var(--card-black); }
  .card-back { top: 470px; background: var(--card-white); }

  .roof-sketch {
    position: absolute;
    left: 0; top: 40px;
    width: 630px; height: 240px;
    background: radial-gradient(ellipse at 55% 55%, rgba(120,120,120,0.22), rgba(60,60,60,0.08) 55%, rgba(13,13,13,0) 75%);
  }
  .brand-mark {
    position: absolute;
    display: flex;
    align-items: center;
    justify-content: center;
    border-radius: 50%;
    text-align: center;
    font-weight: 600;
    line-height: 1.1;
  }
  .card-front .brand-mark {
    left: 275px; top: 60px;
    width: 170px; height: 170px;
    border: 1px solid var(--line-light);
    color: #f2f2f2;
    font-size: 22px;
  }
  .card-back .brand-mark {
    left: 34px; top: 14px;
    width: 100px; height: 100px;
    border: 1px solid #8a8a8a;
    color: var(--ink);
    font-size: 13px;
  }
  .person-name {
    position: absolute;
    left: 40px; top: 122px;
    font-size: 32px;
    font-weight: 700;
    color: var(--ink);
    letter-spacing: 0.5px;
  }
  .name-rule {
    position: absolute;
    left: 40px; top: 168px;
    width: 260px; height: 2px;
    background: var(--sage);
  }
  .address {
    position: absolute;
    left: 40px; top: 176px;
    font-size: 14px;
    line-height: 1.35;
    color: var(--ink-soft);
    letter-spacing: 0.4px;
  }
  .contacts {
    position: absolute;
    left: 30px; top: 228px;
    list-style: none;
    font-size: 14px;
    color: var(--ink-soft);
    letter-spacing: 0.4px;
  }
  .contacts li { display: flex; align-items: center; gap: 8px; height: 22px; }
  .contacts svg { width: 14px; height: 14px; flex: none; }
  .web-accent { color: var(--sage); }
  .bands { position: absolute; inset: 0; pointer-events: none; }
</style>
</head>
<body>
  <section class="card card-front" aria-label="Card front">
    <div class="roof-sketch" role="img" aria-label="Faint sketch of a house roof"></div>
    <div class="brand-mark">Heritage<br>Hollow</div>
  </section>

  <section class="card card-back" aria-label="Card back">
    <svg class="bands" viewBox="0 0 630 360" aria-hidden="true">
      <polygon points="340,360 630,150 630,360" fill="var(--sage)"/>
      <polygon points="450,360 540,360 630,295 630,230" fill="var(--band-dark)"/>
    </svg>
    <div class="brand-mark">Heritage<br>Hollow</div>
    <h1 class="person-name">Maya Torvell</h1>
    <div class="name-rule"></div>
    <p class="address">PO Box Glenwarra<br>NSW 2791</p>
    <ul class="contacts">
      <li>
        <svg viewBox="0 0 16 16" fill="none" stroke="var(--sage)" stroke-width="1.4"><path d="M4 2h2.5l1 3-1.5 1a8 8 0 0 0 4 4l1-1.5 3 1V12a2 2 0 0 1-2 2A10 10 0 0 1 2 4a2 2 0 0 1 2-2z"/></svg>
        02 6481 7395
      </li>
      <li>
        <svg viewBox="0 0 16 16" fill="none" stroke="var(--sage)" stroke-width="1.4"><rect x="1.5" y="3.5" width="13" height="9"/><path d="M1.5 3.5 8 9l6.5-5.5"/></svg>
        maya@kelvadtrading.com.au
      </li>
      <li>
        <svg viewBox="0 0 16 16" fill="none" stroke="var(--sage)" stroke-width="1.4"><circle cx="8" cy="8" r="6.5"/><path d="M1.5 8h13M8 1.5c-3 3.5-3 9.5 0 13M8 1.5c3 3.5 3 9.5 0 13"/></svg>
        <span>www.<span class="web-accent">heritagehollow</span>.com.au</span>
      </li>
    </ul>
  </section>
</body>
</html>
```